Birch Hauling Business Card Design Project

We need a new company business card. We provide professional timber harvesting (logging) and forest management services. I'm open to any creative design. Most company caps and shirts are navy blue and Light grey. Logo does not necessarily have to contain those colors. Logo containing picture of logging equipment, log truck, trees, or logs are acceptable. Be creative. Final logo should communicate our company's pride and professionalism in the East Texas Timber Industry.
Updates

Target Market(s)

Timber owners, sawmills, and forestry professionals

Industry/Entity Type

Business

Requirements
Must have
• Must have Contact Info.
Phone: 555-402-5917
address: PO Box 4830
Pine Hollow, Tx 75990
www.jmbirchhauling.example
jmbirchhauling@mailbox.example
Owner: Jared Marsh

Or design must leave room for this info.

```html
<!DOCTYPE html>
<html lang="en">
<head>
<meta charset="utf-8">
<title>J.M. Birch Hauling Company – Business Card</title>
<link rel="stylesheet" href="https://fonts.googleapis.com/css2?family=Inter:wght@400;500;700;800&display=swap">
<style>
  :root {
    --backdrop: #e9e9e7;
    --card-black: #050505;
    --card-grey: #cfcfcf;
    --card-grey-light: #ececec;
    --accent-blue: #12a3d3;
    --white: #ffffff;
    --ink: #111111;
    --ink-soft: #555555;
    --ghost: rgba(255,255,255,0.35);
  }
  * { box-sizing: border-box; margin: 0; padding: 0; }
  html, body {
    width: 1200px; height: 918px; overflow: hidden;
    background: var(--backdrop);
    font-family: "Inter", Helvetica, Arial, sans-serif;
  }
  .canvas {
    position: relative; width: 1200px; height: 918px;
    display: flex; align-items: center; justify-content: center; gap: 40px;
  }
  .card {
    position: relative; width: 540px; height: 309px; overflow: hidden;
    box-shadow: 0 6px 18px rgba(0,0,0,0.18);
  }

  /* Front: company name */
  .card--front { background: var(--card-black); }
  .front__corner {
    position: absolute; top: 0; left: 160px; width: 34px; height: 20px;
    background: var(--white);
  }
  .front__band {
    position: absolute; top: 0; left: 186px; right: 0; height: 16px;
    background: var(--accent-blue);
  }
  .front__band--thin { top: 20px; left: 200px; height: 6px; }
  .company-name {
    position: absolute; left: 30px; bottom: 26px;
    color: var(--white); font-weight: 400; font-size: 76px;
    line-height: 0.8; letter-spacing: -0.04em; text-transform: uppercase;
  }
  .company-name span { display: block; }

  /* Back: owner & contact */
  .card--back {
    background: radial-gradient(ellipse at 42% 45%, var(--card-grey-light) 0%, var(--card-grey) 70%);
  }
  .back__band {
    position: absolute; top: 0; left: 210px; width: 285px; height: 20px;
    background: var(--accent-blue);
  }
  .back__corner {
    position: absolute; top: 20px; right: 0; width: 70px; height: 18px;
    background: var(--white);
  }
  .back__side-white {
    position: absolute; left: 0; bottom: 0; width: 34px; height: 70px;
    background: var(--white);
  }
  .back__side-blue {
    position: absolute; left: 0; bottom: 24px; width: 26px; height: 72px;
    background: var(--accent-blue);
  }
  .ghost-word {
    position: absolute; left: 120px; top: 36px;
    font-size: 140px; font-weight: 700; letter-spacing: -0.05em;
    color: var(--ghost); line-height: 1;
  }
  .owner { position: absolute; left: 46px; top: 88px; text-align: right; }
  .owner__name {
    font-size: 30px; font-weight: 800; letter-spacing: -0.05em; color: var(--ink); line-height: 1;
  }
  .owner__name .light { font-weight: 500; }
  .owner__title { font-size: 12px; color: var(--ink-soft); letter-spacing: 0.02em; }
  .contact {
    position: absolute; right: 30px; bottom: 26px;
    font-size: 10px; line-height: 1.45; color: var(--ink-soft);
    border-collapse: collapse;
  }
  .contact th { text-align: right; font-weight: 400; padding-right: 4px; white-space: nowrap; }
  .contact th::after { content: " \2022"; }
  .contact td { color: #333; white-space: nowrap; }
</style>
</head>
<body>
<main class="canvas">
  <section class="card card--front" aria-label="Business card front">
    <div class="front__corner"></div>
    <div class="front__band"></div>
    <div class="front__band front__band--thin"></div>
    <h1 class="company-name">
      <span>J.M. Birch</span>
      <span>Hauling</span>
      <span>Company</span>
    </h1>
  </section>

  <section class="card card--back" aria-label="Business card back">
    <div class="back__band"></div>
    <div class="back__corner"></div>
    <div class="back__side-white"></div>
    <div class="back__side-blue"></div>
    <div class="ghost-word" aria-hidden="true">marsh</div>
    <div class="owner">
      <p class="owner__name">jared<span class="light">marsh</span></p>
      <p class="owner__title">company owner</p>
    </div>
    <table class="contact">
      <tr><th>email</th><td>jmbirchhauling@mailbox.example</td></tr>
      <tr><th>phone</th><td>555-402-5917</td></tr>
      <tr><th>web</th><td>www.jmbirchhauling.example</td></tr>
      <tr><th>address</th><td>PO Box 4830 Pine Hollow, Tx 75990</td></tr>
    </table>
  </section>
</main>
</body>
</html>
```